Buch-/E-Book-Cover für Buch zum Thema extremes Klettern und schwere Angsterkrankung
Zielgruppe
Ich bin Autor. in meinem Buch geht es einerseits um extremes Klettern und andererseits um eine schwere Angsterkrankung.
Anstelle eines ausführlichen Briefings lade ich die Buchbeschreibung hoch - da bekommt man am besten ein Gefühl dafür, worum es geht und wer die Zielgruppe ist. Das Buch ist eine Neuauflage daher auch einige Rezensionen der ersten Auflage.
Aufgabenstellung
Ich benötige einen Cover für ein e-book, das später auch für Paperback und Hardcover geeignet ist. Zur Verfügung stehen zwei Fotos, die entweder beide, einzeln oder auch gar nicht verwendet werden können (bitte keine Stock-Fotos.) Die Fotos können beliebig verändert und bearbeitet werden.
Der Buchtitel steht fest - der Untertitel kann sich aber noch ändern.

```html
<!DOCTYPE html>
<html lang="de">
<head>
<meta charset="utf-8">
<title>Die Besteigung des Unbekannten – Cover</title>
<link rel="stylesheet" href="https://fonts.googleapis.com/css2?family=Oswald:wght@300;500;600&family=Roboto:wght@400;500;700&display=swap">
<style>
  :root {
    --page: #ececec;
    --paper: #d3d5dc;
    --paper-dark: #b8bbc5;
    --mint: #e3f1ea;
    --mint-deep: #cadcd2;
    --rock-light: #a9aaa3;
    --rock-dark: #56646e;
    --ink: #161616;
    --subtitle: #8a8a8a;
    --white: #ffffff;
  }
  * { margin: 0; padding: 0; box-sizing: border-box; }
  html, body { width: 851px; height: 1200px; overflow: hidden; background: var(--page); }
  .stage { position: relative; width: 851px; height: 1200px; }
  .front-cover { position: absolute; left: 257px; top: 62px; width: 339px; height: 494px; }
  .wrap-cover { position: absolute; left: 0; top: 610px; width: 851px; height: 590px; overflow: hidden; background: linear-gradient(180deg, var(--paper) 0%, #c9ccd4 100%); }
  .wrap-art { position: absolute; left: 0; top: 0; width: 851px; height: 590px; }
  .wrap-front { position: absolute; left: 448px; top: 0; width: 403px; height: 587px; }
  .back-blurb {
    position: absolute; left: 54px; top: 86px; width: 246px;
    font-family: "Roboto", sans-serif; font-weight: 500; font-size: 8.4px; line-height: 13.1px;
    color: var(--ink);
  }
  .barcode-field { position: absolute; left: 234px; top: 505px; width: 139px; height: 85px; background: var(--white); }
  .spine-author {
    position: absolute; left: 398px; top: 26px; width: 50px; text-align: center;
    font-family: "Oswald", sans-serif; font-weight: 500; font-size: 12px; line-height: 13px; color: var(--ink);
  }
</style>
</head>
<body>
<svg width="0" height="0" style="position:absolute">
  <defs>
    <linearGradient id="mintSky" x1="0" y1="0" x2="0.3" y2="1">
      <stop offset="0" stop-color="var(--mint-deep)"/>
      <stop offset="0.5" stop-color="var(--mint)"/>
      <stop offset="1" stop-color="#eef7f2"/>
    </linearGradient>
    <linearGradient id="rockTone" x1="0" y1="0" x2="1" y2="1">
      <stop offset="0" stop-color="var(--rock-dark)"/>
      <stop offset="0.55" stop-color="#8f938d"/>
      <stop offset="1" stop-color="var(--rock-light)"/>
    </linearGradient>
    <linearGradient id="paperTone" x1="0" y1="0" x2="0" y2="1">
      <stop offset="0" stop-color="var(--paper)"/>
      <stop offset="1" stop-color="var(--paper-dark)"/>
    </linearGradient>
    <symbol id="coverFront" viewBox="0 0 339 494">
      <rect class="cover-paper" width="339" height="494" fill="url(#paperTone)"/>
      <polygon class="cover-sky" points="150,130 298,66 339,60 339,375 86,494 57,494" fill="url(#mintSky)"/>
      <polygon class="cover-photo" role="img" aria-label="Foto: Kletterer in rotem Anzug an überhängender Kalkfelswand"
        points="0,172 14,160 30,168 52,152 70,160 96,146 118,150 140,138 157,143 57,494 0,494" fill="url(#rockTone)"/>
      <text class="cover-author" x="170" y="31" text-anchor="middle" font-family="Oswald, sans-serif" font-weight="300" font-size="19" fill="var(--ink)">Lukas Brendel</text>
      <text class="cover-kicker" x="73" y="70" textLength="194" font-family="Roboto, sans-serif" font-weight="700" font-size="10" fill="var(--ink)">DIE BESTEIGUNG</text>
      <text class="cover-title" x="19" y="150" textLength="301" lengthAdjust="spacingAndGlyphs" font-family="Oswald, sans-serif" font-weight="600" font-size="88" fill="var(--ink)">DES UNBEKANNTEN</text>
      <g class="cover-subtitle" font-family="Oswald, sans-serif" font-weight="500" font-size="27" fill="var(--subtitle)" text-anchor="end">
        <text x="320" y="184">ALS DIE WAND</text>
        <text x="320" y="211">MEIN ZUHAUSE</text>
        <text x="320" y="238">UND DAS</text>
        <text x="320" y="265">ZIMMER</text>
        <text x="320" y="292">MEINE</text>
        <text x="320" y="319">GRÖSSTE</text>
        <text x="320" y="346">ANGST WURDE</text>
      </g>
      <text class="cover-edition" x="322" y="479" text-anchor="end" font-family="Roboto, sans-serif" font-weight="400" font-size="11" fill="var(--ink)">Überarbeitete Neuausgabe</text>
    </symbol>
  </defs>
</svg>

<main class="stage">
  <svg class="front-cover" viewBox="0 0 339 494"><use href="#coverFront"/></svg>

  <section class="wrap-cover">
    <svg class="wrap-art" viewBox="0 0 851 590">
      <polygon class="back-photo" role="img" aria-label="Foto: Nahaufnahme der grauen Kalkfelswand"
        points="0,250 40,236 80,220 120,196 160,176 200,150 240,118 270,96 292,76 300,84 330,150 370,220 420,260 470,250 470,590 0,590" fill="url(#rockTone)"/>
      <text class="spine-title" transform="translate(410,125) rotate(90)" font-family="Oswald, sans-serif" font-size="22" fill="var(--ink)">
        <tspan font-weight="300" textLength="196" lengthAdjust="spacing">DIE BESTEIGUNG</tspan><tspan dx="6" font-weight="600" textLength="142" lengthAdjust="spacingAndGlyphs">DESUNBEKANNTEN</tspan>
      </text>
    </svg>

    <p class="spine-author">Lukas<br>Brendel</p>

    <div class="back-blurb">
      Ein beunruhigend-spannendes Buch von großer sprachlicher Kraft über einen, dem die Wand zum Zuhause und das eigene Zimmer zur größten Angst wurde.“ (BERGWELT)<br>
      Wie kann es dazu kommen, dass einer, der die schwierigsten Kletterrouten beherrscht, im „normalen Leben“ von Angst und Panik derart überwältigt wird, dass er nicht einmal sein Zimmer verlassen kann?<br>
      Lukas Brendel sucht von Jugend an die großen Herausforderungen. Bereits mit 14 Jahren klettert er die schwierigsten Routen im Gebirge und entwickelt sich zu einem Pionier des modernen Freikletterns. Als einem der Ersten gelingen ihm Erstbegehungen im zehnten Schwierigkeitsgrad. Kein Preis ist ihm zu hoch, um die Grenzen des Möglichen noch weiter nach oben zu verschieben.<br>
      Doch dann der jähe Absturz.<br>
      Dem scheinbar unaufhaltsamen Aufstieg beim Klettern folgt der freie Fall im „normalen Leben“. Immer bedrohlicher machen sich Depressionen, Angst und Panik in seinem Leben breit und zwingen ihn zum vollkommenen Rückzug. Die Rückeroberung des Alltages erfordert seine ganze Kraft. Nach all den extremen Kletterrouten, die er bewältigen konnte, wird sein Kampf gegen Angst und Panik, zur größten Herausforderung, der er sich je stellen musste.<br>
      „Der Leser wird Zeuge eines Sturzes, der ins Leere geht. Die Lektüre wird zum körperlichen Erlebnis, man schaudert, fröstelt, leidet.<br>
      RHEINISCHE RUNDSCHAU
    </div>

    <div class="barcode-field"></div>

    <svg class="wrap-front" viewBox="0 0 339 494"><use href="#coverFront"/></svg>
  </section>
</main>
</body>
</html>
```